Communication and Marketing agency needs a new presentation card

We are a group of communication and marketing agencies specialized in companies that are in the logistics and industrial sector. The head agency is TELVANO Grupo and the group consists of 4 agencies: TELVANO Media, TELVANO Digital, TELVANO Research and DifundeEnPantalla. We hace 4 offices in Spain (Madrid, Barcelona, Valencia and Murcia). We are looking for a clean and attractive design that transmits our experience, brand presence in the market and knowledge to those who receive the card.It has to maintain the colors of the logo that is attached.
Target Market(s)
logistics and industrial sector
Marketing department
Contact Information for Business Card
Clean and attractive design

```html
<!DOCTYPE html>
<html lang="es">
<head>
<meta charset="utf-8">
<title>TELVANO Grupo – Business Card</title>
<link rel="stylesheet" href="https://fonts.googleapis.com/css2?family=Titillium+Web:wght@400;600;700&family=Open+Sans:wght@400&display=swap">
<style>
  :root {
    --backdrop: #7c7d84;
    --card-light: #e9e9e9;
    --card-light-edge: #f3f3f3;
    --card-dark: #161616;
    --brand-red: #a3202a;
    --ink: #4a4a4a;
    --paper-white: #e6e6e6;
  }
  * { margin: 0; padding: 0; box-sizing: border-box; }
  html, body { width: 1200px; height: 1144px; overflow: hidden; }
  body { background: var(--backdrop); position: relative; font-family: "Open Sans", sans-serif; }

  .card { position: absolute; left: 255px; width: 691px; height: 394px; }
  .card--front {
    top: 149px;
    background: linear-gradient(135deg, var(--card-light-edge), var(--card-light) 60%, #dedede);
  }
  .card--back { top: 602px; background: var(--card-dark); }

  .wordmark { position: absolute; font-family: "Titillium Web", sans-serif; font-weight: 600; color: var(--brand-red); line-height: 1; text-align: right; }
  .wordmark__name { display: block; letter-spacing: 2px; }
  .wordmark__division { display: block; }

  .card--front .wordmark { left: 53px; top: 150px; width: 294px; }
  .card--front .wordmark__name { font-size: 58px; }
  .card--front .wordmark__division { font-size: 40px; margin-top: 2px; }

  .card--back .wordmark--main { left: 168px; top: 134px; width: 358px; }
  .card--back .wordmark--main .wordmark__name { font-size: 70px; }
  .card--back .wordmark--main .wordmark__division { font-size: 48px; margin-top: 4px; }

  .agencies { position: absolute; top: 316px; left: 0; width: 100%; display: flex; justify-content: center; gap: 16px; }
  .agency { font-family: "Titillium Web", sans-serif; font-weight: 600; font-size: 17px; line-height: 1; text-align: right; width: 102px; }
  .agency span { display: block; }
  .agency__division { font-size: 12px; margin-top: 2px; }
  .agency--light { color: var(--paper-white); }
  .agency--red { color: var(--brand-red); }

  .contact { position: absolute; left: 397px; top: 96px; color: var(--ink); }
  .contact__name { font-family: "Titillium Web", sans-serif; font-weight: 700; font-size: 30px; line-height: 1; color: var(--brand-red); letter-spacing: 0.3px; }
  .contact__role { font-family: "Titillium Web", sans-serif; font-size: 20px; line-height: 1; margin-top: 2px; }
  .contact__rule { width: 71px; height: 1.5px; background: var(--brand-red); margin: 11px 0 12px; }
  .contact__address { font-size: 15.5px; line-height: 22px; }
  .contact__list { list-style: none; font-size: 16px; line-height: 20.5px; }
  .contact__list li { display: flex; align-items: center; gap: 8px; }
  .contact__list svg { width: 12px; height: 12px; fill: var(--brand-red); flex: none; }
</style>
</head>
<body>

<section class="card card--front">
  <div class="wordmark">
    <span class="wordmark__name">TELVANO</span>
    <span class="wordmark__division">Grupo</span>
  </div>

  <div class="contact">
    <h1 class="contact__name">ADRIAN MORELL</h1>
    <p class="contact__role">Founder</p>
    <div class="contact__rule"></div>
    <p class="contact__address">214-220 Calle Lorena<br>28014 Madrid, Spain</p>
    <div class="contact__rule"></div>
    <ul class="contact__list">
      <li>
        <svg viewBox="0 0 24 24" aria-hidden="true"><path d="M6.6 10.8a15 15 0 0 0 6.6 6.6l2.2-2.2a1 1 0 0 1 1-.25 11.4 11.4 0 0 0 3.6.57 1 1 0 0 1 1 1V20a1 1 0 0 1-1 1A17 17 0 0 1 3 4a1 1 0 0 1 1-1h3.5a1 1 0 0 1 1 1c0 1.25.2 2.45.57 3.57a1 1 0 0 1-.25 1z"/></svg>
        (000) 987-654-00
      </li>
      <li>
        <svg viewBox="0 0 24 24" aria-hidden="true"><path d="M2 5h20v2l-10 6L2 7z M2 9l10 6 10-6v10H2z"/></svg>
        info@telvanogrupo.com
      </li>
      <li>
        <svg viewBox="0 0 24 24" aria-hidden="true"><circle cx="12" cy="12" r="10"/></svg>
        www.telvanogrupo.com
      </li>
    </ul>
  </div>
</section>

<section class="card card--back">
  <div class="wordmark wordmark--main">
    <span class="wordmark__name">TELVANO</span>
    <span class="wordmark__division">Grupo</span>
  </div>

  <div class="agencies">
    <div class="agency agency--light"><span>TELVANO</span><span class="agency__division">Research</span></div>
    <div class="agency agency--red"><span>TELVANO</span><span class="agency__division">Media</span></div>
    <div class="agency agency--light"><span>TELVANO</span><span class="agency__division">Digital</span></div>
  </div>
</section>

</body>
</html>
```